Personal Injury Lawyer Billboard

I would like a design created featuring the image of the lawyer centered in the middle of the design.
To the left of the lawyer's image it should read "INJURED?"
To the right of the lawyer's image, it should read "CALL DEAN!"
Under Call Dean, include the phone number 318-555-0187.
At the bottom of the design include the lawyers information "Dean Marlowe Accident & Injury Lawyers"
PLEASE REMOVED THE BACKGROUND IMAGERY OF THE PHOTO SUBMITTED. Also, the colors for this design should match the colors shown in the logo (navy, white and relective soft gold). Please use those color combinations in ways that best stand out.

```html
<!DOCTYPE html>
<html lang="en">
<head>
<meta charset="utf-8">
<title>Dean Marlowe Accident &amp; Injury Lawyers – Billboard</title>
<link rel="stylesheet" href="https://fonts.googleapis.com/css2?family=Cinzel:wght@600&family=Oswald:wght@600&display=swap">
<style>
  :root {
    --backdrop: #9a9a9a;
    --navy: #0a1c45;
    --navy-light: #1b2f66;
    --gold: #c59b36;
    --white: #ffffff;
  }
  html, body {
    margin: 0;
    padding: 0;
    width: 1200px;
    height: 510px;
    overflow: hidden;
    background: var(--backdrop);
  }
  .billboard {
    position: absolute;
    left: 113px;
    top: 66px;
    width: 975px;
    height: 378px;
    background: var(--navy);
    box-shadow: 0 2px 8px rgba(0,0,0,0.35);
    overflow: hidden;
  }
  .headline {
    position: absolute;
    left: 22px;
    top: 134px;
    margin: 0;
    font-family: "Cinzel", serif;
    font-weight: 600;
    font-size: 72px;
    line-height: 1;
    letter-spacing: 2px;
    color: var(--gold);
  }
  .firm-block {
    position: absolute;
    left: 24px;
    top: 0;
    width: 330px;
    height: 378px;
    margin: 0;
    font-family: "Oswald", sans-serif;
    font-weight: 600;
    color: var(--white);
    text-transform: uppercase;
    line-height: 1;
  }
  .firm-block .name-line {
    position: absolute;
    left: 0;
    top: 244px;
    width: 330px;
    font-size: 52px;
    letter-spacing: -0.5px;
    white-space: nowrap;
  }
  .firm-block .practice-line {
    position: absolute;
    left: 0;
    top: 320px;
    width: 330px;
    font-size: 27px;
    letter-spacing: -0.3px;
    white-space: nowrap;
  }
  .gold-rule {
    position: absolute;
    left: 0;
    width: 330px;
    height: 2px;
    background: var(--gold);
  }
  .gold-rule.upper { top: 314px; }
  .gold-rule.lower { top: 361px; }
  .lawyer-portrait {
    position: absolute;
    left: 364px;
    top: 13px;
    width: 274px;
    height: 365px;
    background: linear-gradient(180deg, var(--navy-light) 0%, #15285c 60%, #0f2152 100%);
    border-radius: 90px 90px 0 0;
  }
  .call-to-action {
    position: absolute;
    left: 666px;
    top: 138px;
    margin: 0;
    font-family: "Cinzel", serif;
    font-weight: 600;
    font-size: 48px;
    line-height: 1;
    letter-spacing: 1px;
    color: var(--gold);
    white-space: nowrap;
  }
  .phone {
    position: absolute;
    left: 666px;
    top: 194px;
    display: flex;
    align-items: center;
    gap: 11px;
    font-family: "Cinzel", serif;
    font-weight: 600;
    font-size: 35px;
    color: var(--gold);
    white-space: nowrap;
  }
  .phone-icon {
    width: 38px;
    height: 38px;
    flex: none;
  }
</style>
</head>
<body>
  <main class="billboard">
    <h1 class="headline">INJURED</h1>

    <div class="firm-block">
      <span class="name-line">Dean Marlowe</span>
      <span class="gold-rule upper"></span>
      <span class="practice-line">Accident &amp; Injury Lawyers</span>
      <span class="gold-rule lower"></span>
    </div>

    <div class="lawyer-portrait" role="img" aria-label="Portrait of the lawyer in a navy suit with a raised fist, background removed"></div>

    <h2 class="call-to-action">CALL DEAN</h2>

    <div class="phone">
      <svg class="phone-icon" viewBox="0 0 40 40" aria-hidden="true">
        <circle cx="20" cy="20" r="17.5" fill="none" stroke="var(--gold)" stroke-width="3.5"/>
        <path d="M13.5 11.5c1-1 2.2-.9 2.8.2l1.6 2.9c.5 1 .3 1.9-.5 2.5l-1.2.9c.9 2.3 2.6 4.2 4.9 5.4l1-1.1c.7-.8 1.6-.9 2.5-.4l2.8 1.7c1 .6 1.1 1.8.2 2.8l-1.1 1.2c-1.2 1.3-3.3 1.5-5.3.5-4.4-2.2-7.6-5.6-9.3-9.9-.8-2-.5-4 .8-5.2z" fill="var(--gold)"/>
        <path d="M22 10.5a8 8 0 0 1 7.5 7.5M22 14a4.5 4.5 0 0 1 4 4" fill="none" stroke="var(--gold)" stroke-width="1.8" stroke-linecap="round"/>
      </svg>
      <span class="phone-number">318-555-0187</span>
    </div>
  </main>
</body>
</html>
```